OBK Farcoast Logistics Limited

We need the buissnes card to be very exclusive. As we are all young in our company. We need this to be the gate to make our clients feel deep interest for us.

We are focused in as International Trade advisors, and our products go from Oil Tanker Ships to Rubber balls for dogs.

Our Slogan is Bringing Coasts Closer.
And our main marketing will be through Internet.

We were stablished in 2009 In Mexico and we also have offices in Hong Kong.
We have representatives in China and Europe.

Target Market(s)

Is every company or Individual that wants to develop an International Project or product development or Logistic service of Goods and people.
Some of our current projects are Ship Brokerage, Mine Brokerage, Real State and Product Pormotional development.

Industry/Entity Type

It Company

Requirements
Must have
• Our Logo and slogan, and make the card accoriding to the logo.
Nice to have
• Our Colors

```html
<!DOCTYPE html>
<html lang="en">
<head>
<meta charset="utf-8">
<title>OBK Farcoast Logistics Limited – Business Card</title>
<link rel="stylesheet" href="https://fonts.googleapis.com/css2?family=Open+Sans:wght@400;600;700&display=swap">
<style>
  :root {
    --backdrop: #eceae6;
    --card-blue: #1d82bc;
    --divider-navy: #2b3a8f;
    --brand-green: #8cc63f;
    --brand-blue: #29a3dc;
    --tagline-grey: #5b6670;
    --paper: #ffffff;
    --ink-light: #ffffff;
    --shadow: rgba(0, 0, 0, 0.28);
  }
  html, body {
    margin: 0;
    padding: 0;
    width: 1200px;
    height: 720px;
    overflow: hidden;
    background: var(--backdrop);
    font-family: "Open Sans", Arial, sans-serif;
  }
  .canvas {
    position: relative;
    width: 1200px;
    height: 720px;
  }
  .card {
    position: absolute;
    width: 560px;
    height: 320px;
    box-shadow: 0 10px 24px var(--shadow);
    overflow: hidden;
  }

  /* Contact side */
  .card--contact {
    left: 60px;
    top: 50px;
    display: flex;
    background: var(--card-blue);
  }
  .contact__brand {
    width: 226px;
    background: var(--paper);
    border-right: 5px solid var(--divider-navy);
    display: flex;
    flex-direction: column;
    align-items: center;
    justify-content: center;
  }
  .brand-mark {
    display: flex;
    align-items: center;
    gap: 10px;
  }
  .brand-mark__dot {
    width: 26px;
    height: 26px;
    border-radius: 50%;
    background: var(--brand-blue);
  }
  .brand-mark__name {
    font-weight: 700;
    font-size: 58px;
    line-height: 1;
    color: var(--brand-green);
    letter-spacing: 2px;
  }
  .brand-tagline {
    margin-top: 8px;
    font-size: 13px;
    color: var(--tagline-grey);
  }
  .contact__details {
    flex: 1;
    padding: 34px 0 0 42px;
    color: var(--ink-light);
  }
  .person__name {
    margin: 0;
    font-size: 20px;
    font-weight: 700;
  }
  .person__title {
    margin: 0 0 16px 0;
    font-size: 13px;
  }
  .contact-list {
    list-style: none;
    margin: 0 0 22px 0;
    padding: 0;
    font-size: 15px;
    line-height: 24px;
  }
  .contact-list li {
    display: flex;
    align-items: center;
    gap: 8px;
  }
  .contact-list svg {
    width: 13px;
    height: 13px;
    flex: none;
  }
  .address {
    font-style: normal;
    font-size: 15px;
    line-height: 22px;
  }

  /* Brand side */
  .card--brand {
    left: 580px;
    top: 350px;
    background: var(--card-blue);
    color: var(--ink-light);
  }
  .brand-face__halo {
    position: absolute;
    left: 165px;
    top: 20px;
    width: 230px;
    height: 230px;
    border-radius: 50%;
    background: rgba(255, 255, 255, 0.07);
  }
  .brand-face__lockup {
    position: absolute;
    left: 0;
    right: 0;
    top: 78px;
    text-align: center;
  }
  .brand-face__name {
    font-weight: 700;
    font-size: 110px;
    line-height: 1;
    letter-spacing: 6px;
  }
  .brand-face__tagline {
    margin-top: 6px;
    font-size: 24px;
  }
  .brand-face__web {
    position: absolute;
    left: 0;
    right: 0;
    bottom: 26px;
    text-align: center;
    font-size: 17px;
    letter-spacing: 4px;
  }
</style>
</head>
<body>
<main class="canvas">

  <section class="card card--contact" aria-label="Business card, contact side">
    <div class="contact__brand">
      <div class="brand-mark">
        <span class="brand-mark__dot"></span>
        <span class="brand-mark__name">OBK</span>
      </div>
      <div class="brand-tagline">Bringing Coasts Closer</div>
    </div>
    <div class="contact__details">
      <p class="person__name">Your Name</p>
      <p class="person__title">Title</p>
      <ul class="contact-list">
        <li>
          <svg viewBox="0 0 16 16" aria-hidden="true"><circle cx="8" cy="8" r="7.5" fill="#fff"/><path d="M5 4.5l1.6 1.6-1 1a5 5 0 0 0 3.3 3.3l1-1L11.5 11l-1 1.2C7 12 4 9 3.8 5.5z" fill="#1d82bc"/></svg>
          123-456-0789
        </li>
        <li>
          <svg viewBox="0 0 16 16" aria-hidden="true"><rect x="4" y="1" width="8" height="14" rx="1.5" fill="#fff"/><rect x="5.5" y="3" width="5" height="8" fill="#1d82bc"/></svg>
          123-456-0789
        </li>
        <li>
          <svg viewBox="0 0 16 16" aria-hidden="true"><rect x="1" y="3" width="14" height="10" rx="1" fill="#fff"/><path d="M1.5 3.5L8 9l6.5-5.5" fill="none" stroke="#1d82bc" stroke-width="1.3"/></svg>
          info@farcoastlog.com
        </li>
        <li>
          <svg viewBox="0 0 16 16" aria-hidden="true"><circle cx="8" cy="8" r="7" fill="#fff"/><g fill="none" stroke="#1d82bc" stroke-width="1"><ellipse cx="8" cy="8" rx="3" ry="7"/><path d="M1 8h14M2.5 4.5h11M2.5 11.5h11"/></g></svg>
          www.farcoastlog.com
        </li>
      </ul>
      <address class="address">Street Name, City Name<br>State Zip Code</address>
    </div>
  </section>

  <section class="card card--brand" aria-label="Business card, brand side">
    <div class="brand-face__halo"></div>
    <div class="brand-face__lockup">
      <div class="brand-face__name">OBK</div>
      <div class="brand-face__tagline">Bringing Coasts Closer</div>
    </div>
    <div class="brand-face__web">www.farcoastlog.com</div>
  </section>

</main>
</body>
</html>
```